Business Card Design

We provide services doing multiple jobs in the construction industry.Please note: The company name needs to be ROCK SOLID BUILDING SERVICESAttached logo was an example of what we wanted. Can you change up the colors?

Industry/Entity Type

Construction

Contact Information for Business Card

ROCK SOLID BUILDING SERVICES5401 HUDSON BEND RDAUSTIN, TX 78734(512)243-6854ROCKSOLIDBUILDINGSERVICES@GMAIL.COM

```html
<!DOCTYPE html>
<html lang="en">
<head>
<meta charset="utf-8">
<title>Pearlwood Framing Works – Business Card</title>
<link rel="stylesheet" href="https://fonts.googleapis.com/css2?family=Exo+2:wght@400;500;700&display=swap">
<style>
  :root {
    --navy: #262266;
    --navy-deep: #1b1850;
    --navy-light: #33308a;
    --name-blue: #3a36a0;
    --paper: #f4f4f5;
    --paper-shade: #dcdcde;
    --swoosh: #9a9a9e;
    --text-gray: #4a4a50;
    --white: #ffffff;
    --backdrop: #d7d9de;
  }
  * { box-sizing: border-box; margin: 0; padding: 0; }
  html, body {
    width: 1200px; height: 866px; overflow: hidden;
    background: linear-gradient(160deg, #c9ccd2 0%, var(--backdrop) 55%, #eceef1 100%);
    font-family: "Exo 2", sans-serif;
  }
  .canvas { position: relative; width: 1200px; height: 866px; }
  .card {
    position: absolute; width: 525px; height: 300px; overflow: hidden;
    box-shadow: 0 10px 28px rgba(20, 20, 50, 0.25);
  }
  .card-front {
    left: 50px; top: 150px;
    background: radial-gradient(ellipse at 50% 45%, var(--navy-light) 0%, var(--navy) 55%, var(--navy-deep) 100%);
    display: flex; align-items: center; justify-content: center;
  }
  .brand-name {
    font-weight: 700; letter-spacing: 1px; text-align: center; line-height: 1.05;
  }
  .card-front .brand-name { color: var(--white); font-size: 34px; }
  .card-back { left: 625px; top: 410px; background: var(--paper); }
  .card-back .shapes { position: absolute; inset: 0; }
  .card-back .brand-name {
    position: absolute; left: 34px; top: 108px; width: 190px;
    color: var(--navy); font-size: 24px; text-align: left;
  }
  .holder { position: absolute; right: 22px; top: 40px; text-align: right; }
  .holder-name { color: var(--name-blue); font-size: 21px; font-weight: 500; letter-spacing: 1px; }
  .holder-title { color: var(--text-gray); font-size: 14px; font-style: normal; }
  .address {
    position: absolute; right: 22px; top: 150px; text-align: right;
    color: var(--white); font-size: 13px; line-height: 1.4; font-style: normal;
  }
  .website { position: absolute; right: 22px; top: 212px; color: var(--white); font-size: 13px; }
  .contacts {
    position: absolute; left: 20px; bottom: 12px; list-style: none;
    color: var(--white); font-size: 11.5px; line-height: 1.55;
  }
  .contacts li { display: flex; align-items: center; gap: 8px; }
  .contacts svg { width: 11px; height: 11px; fill: var(--white); }
</style>
</head>
<body>
<main class="canvas">
  <section class="card card-front">
    <p class="brand-name">PEARLWOOD<br>FRAMING WORKS</p>
  </section>

  <section class="card card-back">
    <svg class="shapes" viewBox="0 0 525 300" preserveAspectRatio="none" aria-hidden="true">
      <defs>
        <linearGradient id="paperShade" x1="0" y1="0" x2="1" y2="1">
          <stop offset="0" stop-color="#fafafa"/>
          <stop offset="1" stop-color="#e4e4e6"/>
        </linearGradient>
        <radialGradient id="navyGlow" cx="0.55" cy="0.6" r="0.7">
          <stop offset="0" stop-color="#302c86"/>
          <stop offset="1" stop-color="#1f1c58"/>
        </radialGradient>
      </defs>
      <rect width="525" height="300" fill="url(#paperShade)"/>
      <path d="M0,222 C140,185 300,120 525,78 L525,96 C310,132 150,196 0,240 Z" fill="#9a9a9e"/>
      <path d="M0,236 C140,196 310,130 525,92 L525,300 L0,300 Z" fill="url(#navyGlow)"/>
    </svg>

    <p class="brand-name">PEARLWOOD<br>FRAMING WORKS</p>

    <div class="holder">
      <p class="holder-name">MILES ARDEN</p>
      <p class="holder-title">Managing Director</p>
    </div>

    <address class="address">7732 Fernglen Pass Ln<br>Suite 4B</address>
    <p class="website">www.pearlwoodframing.example</p>

    <ul class="contacts">
      <li><svg viewBox="0 0 12 12"><path d="M2.5 1l2 2.5-1 1.2c.6 1.3 1.6 2.3 2.8 2.8l1.2-1 2.5 2-1 1.8C5 10 2 7 1.2 2z"/></svg>(512)555-0193</li>
      <li><svg viewBox="0 0 12 12"><path d="M3.5 0.5h5v11h-5zM4.5 1.5v8h3v-8z"/></svg>(512)555-0194</li>
      <li><svg viewBox="0 0 12 12"><path d="M1 4h10v7H1zM3 1h6v3H3zM3 6h6v1H3zM3 8h6v1H3z"/></svg>(512)555-0195</li>
      <li><svg viewBox="0 0 12 12"><path d="M0.5 2.5h11v7h-11zM1.5 3.5L6 7l4.5-3.5z"/></svg>miles@mailnest.example</li>
    </ul>
  </section>
</main>
</body>
</html>
```